Website for enterprise software start-up

We need a new Wordpress website. We are an early stage start-up focused on mobile video technology for cellular operators. The audience is strategy, marketing and customer acquisition execs from the operators.

The purpose of the site is to act as a sales brochure and capture leads. A demo app can be downloaded from the current site, want to put that behind a contact form.

Current website is at www.velmora.tv. Similar number of pages. Looking for a clean design template, with minimal customization. Blog will remain as is.

Want to be able to modify the copy via Wordpress. Reference designs I like: quandrix.com, briskfold7metrics.com

Target Market(s)

Mobile operators and MVNOs in the US and Asia Pacific regions

Industry/Entity Type

Business Software

Coding

Coded - Design and coding required

Number of Pages Required

4 page

Font styles to use
Sans Serif

Colors
f78f20

Requirements
Must have
• Form for downloading sample apps.
• Landing page with image, Product, Blog, About, Contact
• Team page

```html
<!DOCTYPE html>
<html lang="en">
<head>
<meta charset="utf-8">
<title>Velmora Media – High Quality Mobile Engagement</title>
<link rel="stylesheet" href="https://fonts.googleapis.com/css2?family=Questrial&family=Lato:ital,wght@0,400;0,700;1,400&display=swap">
<style>
:root{
  --orange:#f78f20;
  --orange-dark:#e2761a;
  --ink:#2b2b2b;
  --text:#4a4a4a;
  --muted:#8a8a8a;
  --paper:#f1f1f1;
  --white:#ffffff;
  --dark:#1d1d1d;
  --navy:#1b2433;
  --line:#d8d8d8;
  --partner:#555555;
  --badge:#c4c4c4;
}
*{box-sizing:border-box;margin:0;padding:0}
html,body{width:1200px;height:2571px;overflow:hidden}
body{position:relative;background:var(--paper);font-family:'Lato',sans-serif;color:var(--text)}
.abs{position:absolute}
h1,h2,h3{font-family:'Questrial',sans-serif;font-weight:400;color:var(--ink)}

/* header */
.site-header{left:0;top:0;width:1200px;height:72px;background:var(--white)}
.brand{left:132px;top:10px;display:flex;align-items:center;gap:10px}
.brand-square{width:48px;height:48px;background:var(--orange)}
.brand-name{font-family:'Questrial',sans-serif;font-size:40px;color:var(--ink);line-height:1}
.main-nav{left:490px;top:0;height:72px;display:flex;align-items:center}
.main-nav a{font-size:13px;font-weight:700;color:var(--ink);text-decoration:none;margin-right:40px}
.main-nav a.active{color:var(--orange)}
.login-btn{left:975px;top:19px;width:91px;height:34px;background:var(--dark);color:var(--white);font-size:13px;font-weight:700;display:flex;align-items:center;justify-content:center}

/* hero */
.hero{left:0;top:72px;width:1200px;height:489px;background:linear-gradient(180deg,#3a3530 0%,#4d4640 45%,#6a5a4b 100%)}
.hero-title{left:132px;top:212px;font-size:48px;line-height:50px;color:var(--white)}
.hero-sub{left:132px;top:328px;font-size:16px;line-height:25px;color:var(--white);font-weight:700;width:500px}
.store-btn{height:60px;background:var(--white);display:flex;align-items:center;gap:12px;padding-left:18px}
.store-icon{width:24px;height:24px;border-radius:50%;background:var(--ink)}
.store-icon.green{background:#8cc43f}
.store-btn small{display:block;font-size:10px;color:var(--text)}
.store-btn b{display:block;font-size:12px;color:var(--ink)}
.notch{width:0;height:0;border-left:34px solid transparent;border-right:34px solid transparent;border-bottom:30px solid var(--paper)}
.notch-mark{width:14px;height:10px;background:var(--orange)}

.hero-phone{left:785px;top:219px;width:281px;height:532px;border-radius:44px;background:linear-gradient(180deg,#f7f7f7,#dcdcdc);box-shadow:0 12px 30px rgba(0,0,0,.25)}
.hero-phone .screen{position:absolute;left:16px;top:60px;width:249px;height:410px;background:linear-gradient(180deg,#3b3f6a 0%,#8a4a5a 30%,#a5593c 55%,#5a3a32 80%,#2a2a3a 100%)}
.hero-phone .home{position:absolute;left:122px;top:478px;width:38px;height:38px;border-radius:50%;border:2px solid #bcbcbc}

/* about */
.about-title{left:135px;top:602px;font-size:30px}
.about-text{left:135px;top:646px;width:600px;font-size:12.5px;line-height:20px}
.btn-orange{background:var(--orange);color:var(--white);display:flex;align-items:center;justify-content:center;font-size:14px}
.about-more{left:135px;top:722px;width:98px;height:32px;font-style:italic}

/* product */
.product{left:0;top:826px;width:1200px;height:477px;background:var(--orange)}
.product-art{left:180px;top:45px;width:317px;height:432px;background:linear-gradient(160deg,#f5d9c4 0%,#e9e9e9 40%,#2c2c2c 60%,#e3c6ae 100%);border-radius:30px 30px 0 0}
.product-title{left:597px;top:62px;font-size:28px;color:var(--ink)}
.product-intro{left:597px;top:117px;width:470px;font-size:12px;font-weight:700;line-height:20px;color:var(--ink)}
.feature-list{left:600px;top:171px;list-style:none;width:560px}
.feature-list li{display:flex;align-items:center;gap:12px;height:45px;font-size:12px;font-weight:700;color:var(--ink)}
.feature-list svg{flex:none}
.slide-arrows{left:600px;top:398px;display:flex;gap:7px}
.slide-arrows span{width:20px;height:20px;background:var(--dark);display:flex;align-items:center;justify-content:center}

/* blog */
.section-title{width:1200px;left:0;text-align:center;font-size:28px}
.blog-image{left:135px;top:1423px;width:360px;height:271px;border:4px solid #dedede;background:linear-gradient(180deg,#1f2a4a 0%,#3c2e5a 35%,#8a2a3a 65%,#c8782c 100%)}
.post-title{left:542px;top:1422px;font-size:20px}
.post-meta{left:542px;top:1466px;font-size:11px;font-style:italic;color:var(--text);display:flex;align-items:center;gap:8px}
.post-body{left:542px;top:1500px;width:510px;font-size:12px;line-height:20px}
.post-body p+p{margin-top:8px}
.btn-dark{left:550px;top:1658px;width:108px;height:36px;background:#3a3a3a;color:var(--white);font-size:13px;font-weight:700;display:flex;align-items:center;justify-content:center}
.divider{left:230px;top:1738px;width:740px;height:3px;background:radial-gradient(ellipse at center,#cfcfcf 0%,rgba(207,207,207,0) 70%)}

/* partners */
.partners{left:0;top:1775px;width:1200px;height:80px}
.partner{position:absolute;top:0;height:80px;display:flex;align-items:center;font-family:'Questrial',sans-serif;font-size:32px;color:var(--partner)}
.badge{width:66px;height:66px;border-radius:50%;background:var(--badge)}

/* downloads */
.downloads{left:0;top:1891px;width:1200px;height:240px;background:linear-gradient(180deg,#1a1a1a,#111)}
.notch-bottom{left:560px;top:2096px;width:80px;height:35px}

/* contact */
.field{background:var(--white);border:1px solid var(--line);font-size:11px;font-style:italic;color:var(--muted);padding:12px 10px}
.submit{left:175px;top:2448px;width:98px;height:34px;font-weight:700;font-size:13px}

/* footer */
.site-footer{left:0;top:2523px;width:1200px;height:48px;background:var(--navy)}
.copyright{left:134px;top:17px;font-size:11px;font-weight:700;color:var(--white)}
.social{left:946px;top:12px;display:flex;gap:8px}
.social span{width:24px;height:24px}
</style>
</head>
<body>

<header class="abs site-header">
  <div class="abs brand"><span class="brand-square"></span><span class="brand-name">velmora</span></div>
  <nav class="abs main-nav">
    <a class="active">Home</a><a>About</a><a>Product</a><a>Our Team</a><a>Blog</a><a>Contact</a>
  </nav>
  <div class="abs login-btn">Login</div>
</header>

<section class="abs hero" role="img" aria-label="Photo of friends relaxing on a beach at dusk"></section>
<h1 class="abs hero-title">High Quality Mobile<br>Engagement™</h1>
<p class="abs hero-sub">We engage mobile audiences with the right video content at the perfect moment.</p>
<div class="abs store-btn" style="left:132px;top:411px;width:187px"><span class="store-icon"></span><span><small>Download it from</small><b>APP HUB</b></span></div>
<div class="abs store-btn" style="left:338px;top:411px;width:187px"><span class="store-icon green"></span><span><small>Download it from</small><b>DROID MARKET</b></span></div>
<div class="abs notch" style="left:566px;top:531px"></div>
<div class="abs notch-mark" style="left:593px;top:548px"></div>

<h2 class="abs about-title">About Velmora Media</h2>
<p class="abs about-text">Velmora Media exists because video consumption is trending away from TV towards mobile, and because mobile media is trending away from pull consumption towards push consumption - where each user is notified of personalized content at the perfect moment.</p>
<div class="abs btn-orange about-more">Read More</div>

<div class="abs hero-phone">
  <div class="screen" role="img" aria-label="Phone screen showing a canyon landscape with a weather widget"></div>
  <div class="home"></div>
</div>

<section class="abs product">
  <div class="abs product-art" role="img" aria-label="Hand holding a phone showing a video analytics app"></div>
  <h2 class="abs product-title">Push Video Notifications</h2>
  <p class="abs product-intro">Personalised flawless HD videos, revealed at the perfect moment, as rich media notifications.</p>
  <ul class="abs feature-list">
    <li><svg width="14" height="14" viewBox="0 0 14 14"><path d="M2 12 L11 3 M5 3 H11 V9" stroke="#b4510a" stroke-width="2" fill="none"/></svg>Reach your mobile audience with beautiful HD thumbnails and in-notification videos.</li>
    <li><svg width="14" height="14" viewBox="0 0 14 14"><path d="M2 12 L11 3 M5 3 H11 V9" stroke="#b4510a" stroke-width="2" fill="none"/></svg>Instant video playback, zero buffering, guaranteed flawless playback - even when offline.</li>
    <li><svg width="14" height="14" viewBox="0 0 14 14"><path d="M2 12 L11 3 M5 3 H11 V9" stroke="#b4510a" stroke-width="2" fill="none"/></svg>Content is personalised based on viewer interests and mobile viewing habits.</li>
    <li><svg width="14" height="14" viewBox="0 0 14 14"><path d="M2 12 L11 3 M5 3 H11 V9" stroke="#b4510a" stroke-width="2" fill="none"/></svg>Monetize with beautiful HD preroll or interstitial ads.</li>
    <li><svg width="14" height="14" viewBox="0 0 14 14"><path d="M2 12 L11 3 M5 3 H11 V9" stroke="#b4510a" stroke-width="2" fill="none"/></svg>Easily added to your existing apps within one hour.</li>
  </ul>
  <div class="abs slide-arrows">
    <span><svg width="8" height="8" viewBox="0 0 8 8"><path d="M6 0 L1 4 L6 8Z" fill="#fff"/></svg></span>
    <span><svg width="8" height="8" viewBox="0 0 8 8"><path d="M2 0 L7 4 L2 8Z" fill="#fff"/></svg></span>
  </div>
</section>

<h2 class="abs section-title" style="top:1344px">Latest Blog</h2>
<div class="abs blog-image" role="img" aria-label="City street at night with bright theatre billboards"></div>
<h3 class="abs post-title">StreamWeek + New Mobile Opportunities</h3>
<div class="abs post-meta"><svg width="12" height="12" viewBox="0 0 12 12"><rect x="1" y="2" width="10" height="9" fill="none" stroke="#888" stroke-width="1.2"/><path d="M1 5H11" stroke="#888"/></svg>May 11, 2016 / Daniel Reyes</div>
<div class="abs post-body">
  <p>The Digital Content StreamWeek events are on again in New York City. Not to be confused with the TV PreviewWeek, the StreamWeek event is a showcase for online content owners to pitch ad spots to brands.</p>
  <p>37 creators including Harlow, Verso, Tubely and Mashwell present their upcoming digital video series. One of the themes emerging this year is the deeper integration of promotional messages into the content.</p>
</div>
<div class="abs btn-dark">Read More</div>
<div class="abs divider"></div>

<div class="abs partners">
  <svg class="abs" style="left:94px;top:34px" width="10" height="12" viewBox="0 0 10 12"><path d="M9 0 L1 6 L9 12Z" fill="#888"/></svg>
  <div class="partner" style="left:136px">Orvanta</div>
  <div class="partner" style="left:390px">Nerida</div>
  <div class="partner" style="left:620px"><span class="badge"></span></div>
  <div class="partner" style="left:760px"><span class="badge"></span></div>
  <div class="partner" style="left:912px">Foxlane</div>
  <svg class="abs" style="left:1088px;top:34px" width="10" height="12" viewBox="0 0 10 12"><path d="M1 0 L9 6 L1 12Z" fill="#888"/></svg>
</div>

<section class="abs downloads" role="img" aria-label="Dark city skyline backdrop"></section>
<h2 class="abs section-title" style="top:1932px;color:#fff">Download Apps</h2>
<div class="abs store-btn" style="left:403px;top:2004px;width:185px"><span class="store-icon"></span><span><small>Download it from</small><b>APP HUB</b></span></div>
<div class="abs store-btn" style="left:608px;top:2004px;width:186px"><span class="store-icon green"></span><span><small>Download it from</small><b>DROID MARKET</b></span></div>
<svg class="abs notch-bottom" viewBox="0 0 80 35"><path d="M0 35 L40 0 L80 35Z" fill="#f1f1f1"/><path d="M2 35 L40 2 L78 35" fill="none" stroke="#f78f20" stroke-width="3"/><rect x="33" y="17" width="14" height="10" fill="none" stroke="#f78f20" stroke-width="1.5"/><path d="M33 17 L40 23 L47 17" fill="none" stroke="#f78f20" stroke-width="1.5"/></svg>

<h2 class="abs section-title" style="top:2172px;color:#111">Quick Contac</h2>
<div class="abs field" style="left:173px;top:2264px;width:274px;height:42px">Your Name</div>
<div class="abs field" style="left:464px;top:2264px;width:261px;height:42px">Your Email</div>
<div class="abs field" style="left:742px;top:2264px;width:276px;height:42px">Subject</div>
<div class="abs field" style="left:173px;top:2343px;width:845px;height:84px">Message</div>
<div class="abs btn-orange submit">Submit</div>

<footer class="abs site-footer">
  <p class="abs copyright">Copyright © 2016 Velmoramedia. All rights reserved.</p>
  <div class="abs social"><span style="background:#3b5998"></span><span style="background:#2ba9e1"></span><span style="background:#d9302a"></span><span style="background:#0e76a8"></span></div>
</footer>

</body>
</html>
```